Business Card for my New Brokerage

Looking to get a business card design for my new Real Estate Brokerage.
I want it with Picture, Phone Number, Email, Website, Office Address
Name and Designation. Please add logo too.

Target Market(s)

Real Estate Investors or Home Buyers

Industry/Entity Type

Real Estate

Contact Information for Business Card

Name, Email, Phone Number, website, email, office address

Colors
EB3D1F
EC4F4E
F09395
F8D3D4
FCEDEE

Requirements
Must have
• Minimalistic, Clean, Modern, Photo
Nice to have
• White and Red Colors

```html
<!DOCTYPE html>
<html lang="en">
<head>
<meta charset="utf-8">
<title>Ember Realty Inc – Business Card</title>
<link href="https://fonts.googleapis.com/css2?family=Montserrat:wght@400;600;700&display=swap" rel="stylesheet">
<style>
  :root {
    --backdrop: #e9ebee;
    --card-white: #eef0f3;
    --brand-red: #cc1d24;
    --accent-gold: #c9a43a;
    --text-grey: #6e6e70;
    --suit-navy: #1f2a44;
    --white: #ffffff;
  }
  * { margin: 0; padding: 0; box-sizing: border-box; }
  html, body {
    width: 1200px; height: 1200px; overflow: hidden;
    background: var(--backdrop);
    font-family: "Montserrat", sans-serif;
  }
  .card {
    position: absolute; left: 227px;
    width: 745px; height: 425px;
    border-radius: 40px; overflow: hidden;
  }
  .card--front { top: 135px; background: var(--card-white); }
  .card--back { top: 640px; background: var(--brand-red); }

  .wordmark { position: absolute; font-weight: 700; line-height: 1; }
  .wordmark__name { display: block; letter-spacing: 1px; }
  .wordmark__sub { display: block; letter-spacing: 6px; }
  .wordmark__dot { display: inline-block; background: var(--accent-gold); vertical-align: top; }

  .card--front .wordmark { left: 27px; top: 58px; color: var(--brand-red); }
  .card--front .wordmark__name { font-size: 84px; }
  .card--front .wordmark__sub { font-size: 22px; margin-top: 10px; padding-left: 60px; }
  .card--front .wordmark__dot { width: 14px; height: 14px; margin-left: 8px; margin-top: 4px; }

  .person { position: absolute; left: 27px; top: 193px; }
  .person__name { font-size: 25px; font-weight: 700; color: var(--brand-red); letter-spacing: 0.5px; }
  .person__title { font-size: 19px; font-weight: 400; color: var(--text-grey); margin-top: 4px; }

  .contacts { position: absolute; left: 27px; top: 278px; list-style: none; }
  .contacts li {
    display: flex; align-items: center; gap: 8px;
    font-size: 19px; color: var(--text-grey); height: 27px;
  }
  .contacts svg { width: 19px; height: 19px; flex: none; }

  .address {
    position: absolute; left: 292px; top: 279px;
    font-size: 19px; color: var(--text-grey); line-height: 27px; font-style: normal;
  }

  .gold-rule { position: absolute; left: 0; top: 376px; width: 470px; height: 4px; background: var(--accent-gold); }
  .red-band { position: absolute; left: 0; top: 383px; width: 470px; height: 42px; background: var(--brand-red); }

  .portrait {
    position: absolute; left: 462px; top: 0; width: 283px; height: 425px;
    background: linear-gradient(180deg, var(--card-white) 0%, #c9ccd2 35%, var(--suit-navy) 70%, #16203a 100%);
  }

  .card--back .wordmark {
    left: 0; right: 0; top: 158px; text-align: center; color: var(--white);
  }
  .card--back .wordmark__name { font-size: 100px; }
  .card--back .wordmark__sub { font-size: 27px; margin-top: 14px; letter-spacing: 8px; }
  .card--back .wordmark__dot { width: 16px; height: 16px; margin-left: 10px; margin-top: 6px; }
</style>
</head>
<body>

<section class="card card--front">
  <div class="wordmark">
    <span class="wordmark__name">EMBER<span class="wordmark__dot"></span></span>
    <span class="wordmark__sub">REALTY INC</span>
  </div>

  <div class="person">
    <h1 class="person__name">DANIEL HARTWELL</h1>
    <p class="person__title">Managing Director</p>
  </div>

  <ul class="contacts">
    <li>
      <svg viewBox="0 0 20 20" aria-hidden="true"><circle cx="10" cy="10" r="10" fill="#cc1d24"/><path d="M6 7.5c0-1 .8-1.8 1.8-1.8h4.4c1 0 1.8.8 1.8 1.8v.8h-2v-.8H8v.8H6zM6.5 9.3h7l.8 5H5.7z" fill="#fff"/></svg>
      555 014 2398
    </li>
    <li>
      <svg viewBox="0 0 20 20" aria-hidden="true"><circle cx="10" cy="10" r="10" fill="#cc1d24"/><rect x="5" y="6.5" width="10" height="7" rx="1" fill="none" stroke="#fff" stroke-width="1.4"/><path d="M5.5 7l4.5 3.6L14.5 7" fill="none" stroke="#fff" stroke-width="1.4"/></svg>
      info@emberrealty.com
    </li>
    <li>
      <svg viewBox="0 0 20 20" aria-hidden="true"><circle cx="10" cy="10" r="10" fill="#cc1d24"/><circle cx="10" cy="10" r="5" fill="none" stroke="#fff" stroke-width="1.4"/><path d="M5 10h10M10 5c-2.5 3-2.5 7 0 10M10 5c2.5 3 2.5 7 0 10" fill="none" stroke="#fff" stroke-width="1.1"/></svg>
      www.emberrealty.com
    </li>
  </ul>

  <address class="address">
    415 Maple Avenue<br>
    Ste 2, Ridgefield<br>
    NH 0352
  </address>

  <div class="gold-rule"></div>
  <div class="red-band"></div>

  <div class="portrait" role="img" aria-label="Portrait photo of the managing director in a navy suit with arms crossed"></div>
</section>

<section class="card card--back">
  <div class="wordmark">
    <span class="wordmark__name">EMBER<span class="wordmark__dot"></span></span>
    <span class="wordmark__sub">REALTY INC</span>
  </div>
</section>

</body>
</html>
```